Cover for a book about building companies without hierarchy

We need to design the cover of our new book. In 2018 we have developed a new organizational design called "Velmorith" which mean equal, just in Latin. This organizational design is hierarchy-free, and it is formed by a radial network of self-organizing teams, where people can take decisions pertaining their job, be autonomous, and contribute to the well being of the larger organization. We published a book in 2018 (see the cover attached), titled: "Velmorith. The Open People-first Structural Model to Flourish in a Shifting Era", where we used the graphic representation of the Velmorith structure in the cover (see attached). The book is intended for top managers, entrepreneurs, businesses.
After 5 years from its launch, we implemented this design in a number of companies and we learned a lot about what works and the challenges. So we decided to publish another book that will be titled: "Velmorith. 5 pillars to shape a people-first office" where we present a revised model, we focus on the principles behind Velmorith and we tell the story of the implementation of Velmorith in Corvellan Italy.
The book cover design must include both front and back, using the template attached.
In the front we need to include: an image or illustration, the Names of the authors (Marisa Tolvengo and Lorenzo Brucani) and the Pelvaro logo.
In the back we shall include: an empty space for the ISDN code as in the template, a short description of the book, the pictures and short bios of the authors .
In the spine we shall include: the title and authors.
Here's the bios:
Marisa Tolvengo is a partner at Pelvaro, a global organizational development firm, a former executive in the corporate setting (including Brindle & Moss and Quibbit! Inc.) and Past President of WPN Global (Worldwide Practitioner Network). She is the author of the book “Inner Compass. The Road to Renewing Guidance” and a FORAx speaker.
Lorenzo Brucani is a partner at Pelvaro and a former manager in multinational settings. He is the co-author of the Calloway Management Journal articles “Why Your Inner Climate Shapes your Output”, “3 Ways to Lift a Gloomy Day”, “Preparing Your Inner Climate for a Holiday Break” and “An Easy Method to Ease Lasting Tension”.
Pictures of the authors attached.
The final versions of the book cover shall be:
- book cover for paperback in English (front and back)
- Book cover for paperback in Italian (front and back)
- Book cover for kindle (only front)

```html
<!DOCTYPE html>
<html lang="en">
<head>
<meta charset="utf-8">
<title>Velmorith – Book Cover Spread</title>
<link rel="stylesheet" href="https://fonts.googleapis.com/css2?family=Poppins:wght@300;400;500;600;700;800&family=Oswald:wght@700&display=swap">
<style>
  :root {
    --navy: #16105e;
    --navy-deep: #120c52;
    --purple: #4a3f9e;
    --green: #5bb833;
    --sky: #1aa3e0;
    --paper: #e4e4e6;
    --paper-light: #f0f0f1;
    --ink: #1e1e24;
    --title-grey: #2c2c34;
    --white: #ffffff;
  }
  * { margin: 0; padding: 0; box-sizing: border-box; }
  html, body { width: 800px; height: 1200px; overflow: hidden; background: var(--white); }
  body { position: relative; font-family: "Poppins", sans-serif; }

  .spread {
    position: absolute; left: 10px; top: 319px;
    width: 1276px; height: 920px;
    transform: scale(0.6113); transform-origin: 0 0;
    background: linear-gradient(180deg, var(--paper-light), var(--paper));
    overflow: hidden;
  }

  .gear-texture { position: absolute; top: 0; height: 836px; }
  .gear-texture--back {
    left: 0; width: 610px;
    background:
      radial-gradient(circle at 8% 62%, rgba(190,190,196,0.45) 0 9%, transparent 16%),
      radial-gradient(circle at 30% 88%, rgba(196,196,202,0.4) 0 8%, transparent 14%),
      radial-gradient(circle at 92% 20%, rgba(205,205,210,0.35) 0 7%, transparent 12%);
  }
  .gear-texture--front {
    left: 668px; width: 608px;
    background:
      radial-gradient(circle at 22% 14%, rgba(200,200,206,0.45) 0 7%, transparent 12%),
      radial-gradient(circle at 90% 10%, rgba(196,196,202,0.45) 0 12%, transparent 19%),
      radial-gradient(circle at 94% 38%, rgba(200,200,206,0.4) 0 8%, transparent 14%),
      radial-gradient(circle at 60% 30%, rgba(210,210,214,0.35) 0 5%, transparent 9%);
  }

  /* ---------- back cover ---------- */
  .back { position: absolute; left: 0; top: 0; width: 610px; height: 836px; text-align: center; color: var(--ink); }
  .wordmark { font-family: "Poppins", sans-serif; font-weight: 400; color: var(--navy); letter-spacing: 1px; line-height: 1; }
  .back .wordmark { position: absolute; left: 0; width: 610px; top: 48px; font-size: 78px; }
  .back-subtitle { position: absolute; left: 0; width: 610px; top: 128px; font-size: 19px; font-weight: 400; line-height: 24px; text-transform: uppercase; }
  .blurb { position: absolute; left: 55px; width: 500px; top: 184px; font-size: 13.4px; line-height: 16.8px; font-weight: 400; }
  .blurb p + p { margin-top: 16px; }

  .author-card { position: absolute; left: 59px; width: 501px; height: 164px; border-radius: 16px; overflow: hidden; color: var(--white); text-align: left; }
  .author-card--first { top: 424px; background: var(--purple); }
  .author-card--second { top: 607px; background: var(--navy-deep); }
  .author-photo { position: absolute; left: 0; bottom: 0; width: 165px; height: 164px; }
  .author-card--first .author-photo { background: linear-gradient(180deg, var(--purple) 0%, #8e6f9e 35%, #c9574f 70%, #b8443f 100%); }
  .author-card--second .author-photo { background: linear-gradient(180deg, var(--navy-deep) 0%, #5b4f7a 35%, #d8d6dc 70%, #eeeef2 100%); }
  .author-name { position: absolute; left: 172px; top: 12px; font-size: 19px; font-weight: 700; }
  .author-card--first .author-name { color: var(--green); }
  .author-card--second .author-name { color: var(--sky); }
  .author-bio { position: absolute; left: 172px; top: 45px; width: 315px; font-size: 11px; line-height: 13.3px; }

  /* ---------- spine ---------- */
  .spine { position: absolute; left: 610px; top: 0; width: 58px; height: 920px; background: var(--navy); }
  .spine-text { position: absolute; top: 40px; left: 0; width: 58px; height: 860px; writing-mode: vertical-rl; display: flex; align-items: center; }
  .spine .wordmark { color: var(--white); font-size: 30px; font-weight: 300; }
  .spine-title { margin-top: 14px; color: var(--green); font-size: 17px; font-weight: 700; line-height: 19px; text-transform: uppercase; text-align: left; }
  .spine-authors { margin-top: 110px; color: var(--white); font-size: 14px; font-weight: 700; text-transform: uppercase; }

  /* ---------- front cover ---------- */
  .front { position: absolute; left: 668px; top: 0; width: 608px; height: 836px; }
  .publisher { position: absolute; left: 0; width: 608px; top: 40px; text-align: center; font-size: 22px; font-weight: 600; color: var(--navy); letter-spacing: 1px; }
  .front .wordmark { position: absolute; left: 0; width: 608px; top: 96px; text-align: center; font-size: 80px; }
  .cover-photo {
    position: absolute; left: 0; top: 372px; width: 608px; height: 464px;
    background:
      radial-gradient(ellipse 22% 30% at 20% 72%, rgba(236,228,214,0.95), transparent 70%),
      radial-gradient(ellipse 16% 34% at 37% 50%, rgba(70,70,78,0.9), transparent 70%),
      radial-gradient(ellipse 18% 26% at 56% 68%, rgba(196,192,172,0.95), transparent 70%),
      radial-gradient(ellipse 14% 28% at 72% 46%, rgba(40,46,80,0.85), transparent 70%),
      radial-gradient(ellipse 15% 26% at 88% 66%, rgba(178,182,190,0.95), transparent 70%),
      linear-gradient(180deg, rgba(228,228,230,0) 0%, #dcd9d4 12%, #cfcac3 40%, #b7a89a 80%, #8a6f5a 100%);
  }
  .big-number { position: absolute; left: 52px; top: 214px; font-family: "Oswald", sans-serif; font-weight: 700; font-size: 222px; line-height: 1; color: var(--green); }
  .title { position: absolute; left: 161px; top: 204px; color: var(--navy); }
  .title-lead { font-size: 45px; font-weight: 700; line-height: 40px; color: var(--title-grey); text-transform: uppercase; letter-spacing: 0.5px; }
  .title-main { margin-top: 6px; font-family: "Oswald", sans-serif; font-weight: 700; font-size: 67px; line-height: 70px; transform: scaleY(1.05); transform-origin: 0 0; text-transform: uppercase; }

  /* ---------- bottom band ---------- */
  .band { position: absolute; left: 0; top: 836px; width: 1276px; height: 84px; background: var(--navy-deep); }
  .band-publisher { position: absolute; left: 70px; top: 24px; color: var(--white); font-size: 22px; font-weight: 600; letter-spacing: 1px; }
  .band-authors { position: absolute; left: 668px; width: 608px; top: 26px; text-align: center; color: var(--white); font-size: 22px; font-weight: 700; text-transform: uppercase; }
</style>
</head>
<body>
<div class="spread">

  <div class="gear-texture gear-texture--back" role="img" aria-label="Faint grey gear and cog pattern in the background"></div>
  <div class="gear-texture gear-texture--front" role="img" aria-label="Faint grey gear and cog pattern in the background"></div>

  <section class="back">
    <div class="wordmark">Velmorith</div>
    <div class="back-subtitle">5 pillars to shape a<br>people-first office</div>
    <div class="blurb">
      <p>Is your organization failing to create the environment where real collaboration, innovation and speed are a natural habit and people are truly engaged?</p>
      <p>What if the real key to all this was a radical change in the way your organization is actually structured?</p>
      <p>The authors’ 15+ year experience in change initiatives, together with the outcomes of an extensive qualitative and quantitative research, led to the creation of Velmorith. Velmorith is a revolutionary organizational model based on a radial and peer- based structure of self-organized and coordinated teams that overcome the limits of the hierarchy and expands individual, team and organizational potential</p>
    </div>

    <article class="author-card author-card--first">
      <div class="author-photo" role="img" aria-label="Portrait photo of author Marisa Tolvengo"></div>
      <h3 class="author-name">Marisa Tolvengo</h3>
      <p class="author-bio">Marisa Tolvengo is a partner at Pelvaro, a global organizational development firm, a former executive in the corporate setting (including Brindle &amp; Moss and Quibbit! Inc.) and Past President of WPN Global (Worldwide Practitioner Network). She is the author of the book “Inner Compass. The Road to Renewing Guidance” and a FORAx speaker.</p>
    </article>

    <article class="author-card author-card--second">
      <div class="author-photo" role="img" aria-label="Portrait photo of author Lorenzo Brucani"></div>
      <h3 class="author-name">Lorenzo Brucani</h3>
      <p class="author-bio">Lorenzo Brucani is a partner at Pelvaro and a former manager in multinational settings. He is the co-author of the Calloway Management Journal articles “Why Your Inner Climate Shapes your Output”, “3 Ways to Lift a Gloomy Day”, “Preparing Your Inner Climate for a Holiday Break” and “An Easy Method to Ease Lasting Tension”.</p>
    </article>
  </section>

  <section class="spine">
    <div class="spine-text">
      <span class="wordmark">Velmorith</span>
      <span class="spine-title">5 pillars to shape a<br>people-first office</span>
      <span class="spine-authors">Marisa Tolvengo - Lorenzo Brucani</span>
    </div>
  </section>

  <section class="front">
    <div class="publisher">PELVARO</div>
    <div class="wordmark">Velmorith</div>
    <div class="cover-photo" role="img" aria-label="Photo of a smiling team of colleagues gathered around a table with a tablet in a bright office"></div>
    <div class="big-number">5</div>
    <div class="title">
      <div class="title-lead">Pillars to<br>shape a</div>
      <div class="title-main">People-first<br>office</div>
    </div>
  </section>

  <div class="band">
    <div class="band-publisher">PELVARO</div>
    <div class="band-authors">Marisa Tolvengo - Lorenzo Brucani</div>
  </div>

</div>
</body>
</html>
```